Modern Verdell Tree Care Website

I need a website for a full service Tree Care company. The company provides tree pruning, tree removal, tree preservation, emergency services, stump grinding, and emergency tree services.

Target Market(s)

Customers that need tree services

Industry/Entity Type

Landscaping, Tree Services

Coding

Coded - Design and coding required

Number of Pages Required

5+ page

Font styles to use
Sans Serif

Requirements
Must have
• Good clean design that showcases the services the company provides.
Nice to have
• Services page; contact form, blog, home page, about page

```html
<!DOCTYPE html>
<html lang="en">
<head>
<meta charset="utf-8">
<title>Verdell Tree Care</title>
<link href="https://fonts.googleapis.com/css2?family=Inter:wght@400;500;600;700;800&display=swap" rel="stylesheet">
<style>
:root{
  --forest:#2f4a25;
  --forest-deep:#1f3118;
  --lime:#7cc243;
  --orange:#f6a531;
  --cream:#f6f4d2;
  --lime-text:#cfe06a;
  --gold:#f2cf47;
  --ink:#1c1c1c;
  --muted:#4a4a4a;
  --white:#ffffff;
  --star:#f4c542;
}
*{margin:0;padding:0;box-sizing:border-box}
html,body{width:1200px;height:2853px;overflow:hidden}
body{position:relative;font-family:"Inter",sans-serif;color:var(--ink);background:var(--white)}
.abs{position:absolute}
a{color:inherit;text-decoration:none}

/* header */
.brand{left:57px;top:30px;display:flex;align-items:center;gap:10px;font-weight:800;font-size:20px;color:var(--forest)}
.brand-mark{width:26px;height:26px;background:var(--lime)}
.nav{left:347px;top:38px;font-size:12px;color:#555}
.nav span{position:absolute;white-space:nowrap}
.pill{display:flex;align-items:center;justify-content:center;gap:8px;border-radius:20px;font-size:12px;font-weight:600}
.pill-lime{background:var(--lime);color:var(--white)}
.pill-dark{background:var(--forest);color:var(--white)}
.pill-outline{border:1.5px solid var(--forest);color:var(--forest);background:var(--white)}
.pill-cream{background:var(--cream);color:var(--forest)}

/* hero */
.hero-title{left:135px;top:160px;font-size:50px;line-height:57px;font-weight:800;color:var(--forest);letter-spacing:-0.5px}
.hero-title em{font-style:normal;color:var(--orange)}
.hero-lead{left:140px;top:281px;width:520px;font-size:15.5px;line-height:21px;font-weight:500}
.hero-photo{left:712px;top:114px;width:320px;height:320px;border-radius:50%;background:radial-gradient(circle at 50% 60%,#6f8a4a,#3f5a2b 55%,#24361a)}
.social-dot{width:38px;height:38px;border-radius:50%;background:var(--forest)}

/* intro */
.photo{border:2px solid var(--cream);border-radius:10px}
.intro-title{left:531px;top:595px;font-size:28px;font-weight:700;color:var(--lime-text)}
.intro-sub{left:531px;top:633px;font-size:17px;font-weight:600;color:var(--white)}
.intro-text{left:531px;top:666px;width:545px;font-size:13px;line-height:21px;color:#e8eee2}

/* services */
.svc-label{left:128px;top:1052px;font-size:15.5px;font-weight:600;color:var(--lime)}
.svc-title{left:128px;top:1073px;font-size:29px;font-weight:700;color:var(--forest)}
.svc-text{left:128px;top:1120px;width:420px;font-size:13.4px;line-height:21px;color:var(--muted)}
.slide{border-radius:12px}

/* features */
.band{left:0;top:1433px;width:1200px;height:172px;background:var(--forest)}
.feature{width:140px;text-align:center;color:var(--white);font-size:11px;line-height:13px;font-weight:500}
.feature svg{display:block;margin:0 auto 10px}

/* testimonials */
.t-title{left:0;top:1671px;width:1216px;text-align:center;font-size:21px;font-weight:700;color:var(--forest)}
.t-sub{left:0;top:1699px;width:1216px;text-align:center;font-size:13.4px;line-height:21px;color:#444}
.card-clip{left:96px;top:1770px;width:1009px;height:230px;overflow:hidden}
.card{position:absolute;width:388px;height:208px;background:var(--white);border:1px solid #ddd;box-shadow:0 3px 6px rgba(0,0,0,.12);padding:26px 28px}
.card p{font-size:13.4px;line-height:21px;color:#333}
.card .more{position:absolute;left:28px;top:118px;font-size:11.5px;color:#555}
.card .stars{position:absolute;right:26px;top:108px;display:flex;gap:11px}
.card .who{position:absolute;left:28px;top:143px;display:flex;align-items:center;gap:12px;font-size:13.4px;font-weight:500;white-space:nowrap}
.avatar{width:44px;height:44px;border-radius:50%;background:linear-gradient(160deg,#9fd4c4,#6fa99a)}

/* consult */
.consult{left:0;top:2074px;width:1200px;height:364px;background:var(--forest)}
.consult-photo{left:86px;top:2115px;width:416px;height:277px;border:2px solid var(--cream);border-radius:14px;background:linear-gradient(135deg,#6a5a2e,#4a4325 50%,#2d3a1f)}
.consult-title{left:120px;top:2142px;font-size:20.5px;font-weight:700;color:var(--white)}
.consult-text{left:122px;top:2172px;width:320px;font-size:13.4px;line-height:21px;color:#f0f0f0}
.field{background:var(--white);border-radius:9px;font-size:13px;color:#bbb;padding:9px 16px}

/* footer */
.footer{left:0;top:2527px;width:1200px;height:326px;background:var(--forest-deep)}
.f-brand{left:65px;top:2588px;display:flex;align-items:center;gap:14px;color:var(--white)}
.f-brand-mark{width:52px;height:52px;background:var(--white)}
.f-brand-name{display:flex;flex-direction:column;font-weight:700;line-height:1}
.f-brand-name b{font-size:34px;font-weight:700;letter-spacing:1px}
.f-brand-name span{font-size:20px;font-weight:700;letter-spacing:3px;margin-top:6px}
.f-social{width:42px;height:42px;border-radius:50%;background:var(--cream)}
.f-head{font-size:16px;font-weight:700;color:var(--gold)}
.f-item{font-size:17px;color:var(--white)}
.f-news{left:814px;top:2580px;font-size:13.5px;font-weight:700;color:var(--white)}
.rule{left:57px;top:2791px;width:1085px;height:1px;background:#8f8f3a}
.copy{left:0;top:2809px;width:1200px;text-align:center;font-size:13.4px;color:#e8e8e8}
</style>
</head>
<body>

<!-- header -->
<div class="abs brand"><span class="brand-mark"></span>Verdell Tree Care</div>
<nav class="abs nav" aria-label="Main">
  <span style="left:0;font-weight:600;color:#333">Home</span>
  <span style="left:84px">About</span>
  <span style="left:168px">Tree Care Services ⌄</span>
  <span style="left:342px">Expert Advice &amp; Consulting</span>
</nav>
<a class="abs pill pill-lime" style="left:1003px;top:30px;width:140px;height:31px">
  <svg width="13" height="13" viewBox="0 0 24 24" fill="#fff"><path d="M6.6 10.8a15 15 0 006.6 6.6l2.2-2.2a1 1 0 011-.25 11.4 11.4 0 003.6.6 1 1 0 011 1V20a1 1 0 01-1 1A17 17 0 013 4a1 1 0 011-1h3.5a1 1 0 011 1c0 1.25.2 2.45.6 3.6a1 1 0 01-.25 1z"/></svg>(555) 014-3827</a>

<!-- hero -->
<svg class="abs" style="left:0;top:380px" width="1200" height="580" viewBox="0 380 1200 580">
  <path d="M0,388 Q600,650 1200,449 L1200,960 L0,960 Z" fill="var(--forest)"/>
  <circle cx="599" cy="459" r="1.6" fill="#a9b79a"/>
  <path d="M599,466 V482 M593,476 L599,482 L605,476" stroke="#a9b79a" stroke-width="1.4" fill="none"/>
</svg>
<h1 class="abs hero-title">Call <em>VERDELL</em> For All<br>Your Tree Care Needs</h1>
<p class="abs hero-lead">Discover Verdell, Your Reliable Choice for All Your Tree Care Essentials, Ensuring Your Greenery Thrives.</p>
<a class="abs pill pill-dark" style="left:139px;top:339px;width:142px;height:30px">
  <svg width="13" height="13" viewBox="0 0 24 24" fill="#fff"><path d="M6.6 10.8a15 15 0 006.6 6.6l2.2-2.2a1 1 0 011-.25 11.4 11.4 0 003.6.6 1 1 0 011 1V20a1 1 0 01-1 1A17 17 0 013 4a1 1 0 011-1h3.5a1 1 0 011 1c0 1.25.2 2.45.6 3.6a1 1 0 01-.25 1z"/></svg>(555) 014-3827</a>
<a class="abs pill pill-outline" style="left:293px;top:339px;width:141px;height:30px">Explore Verdell
  <svg width="18" height="8" viewBox="0 0 18 8"><path d="M0 4H16M12 1L16 4L12 7" stroke="currentColor" stroke-width="1.3" fill="none"/></svg></a>

<svg class="abs" style="left:696px;top:98px" width="352" height="352" viewBox="0 0 352 352">
  <path d="M143 8 A168 168 0 1 1 30 90" stroke="var(--lime)" stroke-width="6" fill="none" stroke-linecap="round"/>
</svg>
<div class="abs hero-photo" role="img" aria-label="Photo of a wooden boardwalk winding through a lush forest of tall trees and ferns"></div>

<div class="abs social-dot" style="left:1066px;top:158px" role="img" aria-label="Email">
  <svg width="38" height="38" viewBox="0 0 38 38"><rect x="11" y="13" width="16" height="12" rx="2" stroke="#fff" stroke-width="1.6" fill="none"/><path d="M11 14l8 6 8-6" stroke="#fff" stroke-width="1.6" fill="none"/></svg></div>
<div class="abs social-dot" style="left:1066px;top:215px" role="img" aria-label="Social profile"></div>
<div class="abs social-dot" style="left:1066px;top:272px" role="img" aria-label="Social profile"></div>
<div class="abs social-dot" style="left:1066px;top:329px" role="img" aria-label="Social profile"></div>

<!-- intro -->
<div class="abs photo" style="left:143px;top:573px;width:328px;height:186px;background:linear-gradient(135deg,#4d6b8a,#5d6b3a 45%,#6a4e30)" role="img" aria-label="Photo of hands planting a young tree beside a watering can"></div>
<div class="abs photo" style="left:143px;top:767px;width:102px;height:97px;background:linear-gradient(160deg,#7a9a4a,#c76a2e 55%,#3c6a2c)" role="img" aria-label="Photo of a worker trimming a hedge"></div>
<div class="abs photo" style="left:255px;top:767px;width:102px;height:97px;background:linear-gradient(160deg,#5d7a43,#8aa66a 60%,#3f5a2f)" role="img" aria-label="Photo of a garden being watered"></div>
<div class="abs photo" style="left:368px;top:767px;width:102px;height:97px;background:linear-gradient(160deg,#6c5a3a,#9e8a58 50%,#c33a22)" role="img" aria-label="Photo of pruning shears cutting a branch"></div>

<h2 class="abs intro-title">Introducing VERDELL</h2>
<p class="abs intro-sub">Our Ultimate Destination for Exceptional Tree Care Services</p>
<p class="abs intro-text">At Verdell Tree Care, we are more than just a tree service company, we are stewards of our beautiful trees. With a passion deeply rooted in arboriculture, we embark on a mission to promote the health, beauty, and safety of your trees and landscapes. Whether it's expert tree trimming to enhance aesthetics, meticulous tree removal to mitigate hazards, or comprehensive tree health assessments to ensure safety, we approach each task with unwavering dedication and attention to detail.</p>
<a class="abs pill pill-cream" style="left:532px;top:805px;width:121px;height:30px">Read More</a>

<!-- services -->
<p class="abs svc-label">Choose Your Tree Care Services</p>
<h2 class="abs svc-title">Tree Triming</h2>
<p class="abs svc-text">Lorem ipsum dolor sit amet, consectetur adipiscing elit, sed do eiusmod tempor incididunt ut labore et dolore magna aliqua. Ut enim ad minim veniam, quis nostrud exercitation ullamco laboris nisi ut aliquip ex ea commodo consequat. Duis aute irure dolor in reprehenderit in voluptate velit esse cillum dolore eu fugiat nulla pariatur. Excepteur sint occaecat cupidatat non proident, sunt in culpa qui officia deserunt mollit anim id est laborum.</p>
<a class="abs pill pill-dark" style="left:128px;top:1287px;width:121px;height:31px">Service Detail</a>
<a class="abs pill pill-outline" style="left:258px;top:1287px;width:122px;height:31px">Book Service</a>

<div class="abs slide" style="left:608px;top:1067px;width:100px;height:208px;background:linear-gradient(160deg,#4f7a33,#8aa86a 50%,#2f4a22)" role="img" aria-label="Photo of pruning shears among green leaves"></div>
<div class="abs slide" style="left:955px;top:1067px;width:90px;height:208px;background:linear-gradient(160deg,#c9b68a,#5b9ac4 55%,#5d8a3a)" role="img" aria-label="Photo of a child watering plants"></div>
<div class="abs slide" style="left:698px;top:1018px;width:268px;height:306px;border:1px solid var(--cream);background:linear-gradient(160deg,#4e8ec8,#6a5a3e 50%,#2f3a28)" role="img" aria-label="Photo of an arborist in a helmet cutting a tree trunk with a chainsaw"></div>
<svg class="abs" style="left:780px;top:1338px" width="104" height="12" viewBox="0 0 104 12">
  <path d="M46 6H2M7 1L2 6L7 11" stroke="#999" stroke-width="1.3" fill="none"/>
  <path d="M58 6H102M97 1L102 6L97 11" stroke="#222" stroke-width="1.5" fill="none"/>
</svg>

<!-- features -->
<div class="abs band"></div>
<div class="abs feature" style="left:156px;top:1460px">
  <svg width="68" height="70" viewBox="0 0 68 70" fill="none" stroke="#fff" stroke-width="2"><rect x="10" y="10" width="40" height="52" rx="3"/><path d="M18 24h24M18 34h24M18 44h16"/><circle cx="22" cy="14" r="10" fill="var(--forest)"/><path d="M17 14l4 4 6-7"/><path d="M44 56l14-16 5 5-14 16-7 2z"/></svg>Licensed<br>and Insured</div>
<div class="abs feature" style="left:300px;top:1460px">
  <svg width="68" height="70" viewBox="0 0 68 70" fill="none" stroke="#fff" stroke-width="2"><circle cx="36" cy="32" r="26"/><path d="M8 40c4 12 12 18 20 20l4-6-8-6-4 4c-4-3-6-6-7-10l4-4-5-8z"/><text x="22" y="38" fill="#fff" stroke="none" font-family="Inter,sans-serif" font-size="16">24/7</text></svg>24 Hours<br>Emergency<br>Services</div>
<div class="abs feature" style="left:455px;top:1460px">
  <svg width="72" height="70" viewBox="0 0 72 70" fill="none" stroke="#fff" stroke-width="2"><path d="M6 30l6-14h34l6 14z"/><path d="M6 30v6h46v-6M10 36v28h38V36"/><rect x="14" y="44" width="12" height="10"/><rect x="32" y="44" width="10" height="20"/><path d="M58 34c-6-8-10-12-10-18a10 10 0 0120 0c0 6-4 10-10 18z"/><circle cx="58" cy="16" r="4"/></svg>Locally Owned<br>and Operated</div>
<div class="abs feature" style="left:607px;top:1460px">
  <svg width="72" height="74" viewBox="0 0 72 74" fill="none" stroke="#fff" stroke-width="2"><circle cx="36" cy="22" r="6"/><circle cx="18" cy="28" r="5"/><circle cx="54" cy="28" r="5"/><path d="M26 44c0-8 4-12 10-12s10 4 10 12M8 46c0-6 4-10 10-10M64 46c0-6-4-10-10-10"/><circle cx="36" cy="58" r="8"/><circle cx="36" cy="58" r="3"/><path d="M36 4l2 4h4l-3 3 1 4-4-2-4 2 1-4-3-3h4zM16 8l1 3h3l-2 2 1 3-3-2-3 2 1-3-2-2h3zM56 8l1 3h3l-2 2 1 3-3-2-3 2 1-3-2-2h3z"/></svg>Professional<br>Work</div>
<div class="abs feature" style="left:750px;top:1460px">
  <svg width="72" height="74" viewBox="0 0 72 74" fill="none" stroke="#fff" stroke-width="2"><path d="M20 24a14 14 0 0128 0"/><path d="M16 24h36v4H16zM34 10v8"/><path d="M22 30c0 8 5 14 12 14s12-6 12-14"/><path d="M8 70c0-14 10-22 26-22 4 0 8 .5 10 1.5"/><path d="M56 46l12 5v8c0 7-5 11-12 14-7-3-12-7-12-14v-8z"/><path d="M51 59l4 4 7-8"/></svg>Safety Is Our<br>No 1 Priority</div>
<div class="abs feature" style="left:886px;top:1460px">
  <svg width="72" height="76" viewBox="0 0 72 76" fill="none" stroke="#fff" stroke-width="2"><circle cx="24" cy="20" r="12"/><circle cx="24" cy="20" r="6"/><circle cx="52" cy="44" r="14"/><path d="M52 36v8l6 4"/><circle cx="26" cy="44" r="6"/><path d="M12 72c0-10 6-16 14-16s14 6 14 16"/></svg>Free<br>Estimates</div>

<!-- testimonials -->
<h2 class="abs t-title">What Client Say About Us</h2>
<p class="abs t-sub">Lorem ipsum dolor sit amet, consectetur adipiscing elit, sed do eiusmod tempor<br>incididunt ut labore et dolore magna aliqua.</p>
<svg class="abs" style="left:1066px;top:1741px" width="42" height="12" viewBox="0 0 42 12">
  <path d="M14 6H2M6 2L2 6L6 10" stroke="#aaa" stroke-width="1.4" fill="none"/>
  <path d="M28 6H40M36 2L40 6L36 10" stroke="#222" stroke-width="1.6" fill="none"/>
</svg>

<div class="abs card-clip">
  <div class="card" style="left:0;top:8px">
    <p>Lorem ipsum dolor sit amet, consectetur adipiscing elit, sed do eiusmod tempor incididunt ut labore et dolore magna aliqua.</p>
    <span class="more">Read More</span>
    <div class="stars"><svg width="156" height="24" viewBox="0 0 156 24" fill="var(--star)"><path id="st" d="M12 0l3.5 8 8.5.8-6.5 5.7 2 8.5L12 18.6 4.5 23l2-8.5L0 8.8 8.5 8z"/><use href="#st" x="33"/><use href="#st" x="66"/><use href="#st" x="99"/><use href="#st" x="132"/></svg></div>
    <div class="who"><span class="avatar" role="img" aria-label="Client portrait"></span>Mira Santoro</div>
  </div>
  <div class="card" style="left:426px;top:5px">
    <p>Lorem ipsum dolor sit amet, consectetur adipiscing elit, sed do eiusmod tempor incididunt ut labore et dolore magna aliqua.</p>
    <span class="more">Read More</span>
    <div class="stars"><svg width="156" height="24" viewBox="0 0 156 24" fill="var(--star)"><use href="#st"/><use href="#st" x="33"/><use href="#st" x="66"/><use href="#st" x="99"/><use href="#st" x="132"/></svg></div>
    <div class="who"><span class="avatar" style="background:linear-gradient(160deg,#e3a56a,#b8733e)" role="img" aria-label="Client portrait"></span>Daniel Osei</div>
  </div>
  <div class="card" style="left:851px;top:3px">
    <p>Lorem ipsum dolor sit amet, consectetur adipiscing elit, sed do eiusmod tempor incididunt ut labore et dolore magna aliqua.</p>
    <span class="more">Read More</span>
    <div class="who"><span class="avatar" role="img" aria-label="Client portrait"></span>Mira Santoro</div>
  </div>
</div>

<!-- consulting -->
<div class="abs consult"></div>
<div class="abs consult-photo" role="img" aria-label="Photo of an older man talking with a consultant outdoors in autumn light"></div>
<h2 class="abs consult-title">Seek For Expert Advice Consulting</h2>
<p class="abs consult-text">Lorem ipsum dolor sit amet, consectetur adipiscing elit, sed do eiusmod tempor incididunt ut labore et dolore magna aliqua.</p>
<div class="abs field" style="left:542px;top:2130px;width:267px;height:34px">First Name</div>
<div class="abs field" style="left:831px;top:2130px;width:253px;height:34px">Last Name</div>
<div class="abs field" style="left:542px;top:2181px;width:267px;height:34px">Email Address</div>
<div class="abs field" style="left:831px;top:2181px;width:253px;height:34px">Phone</div>
<div class="abs field" style="left:542px;top:2235px;width:542px;height:83px">Messages</div>
<a class="abs pill pill-cream" style="left:962px;top:2342px;width:122px;height:35px;border-radius:9px">Submit</a>

<!-- footer -->
<footer class="abs footer"></footer>
<div class="abs f-brand"><span class="f-brand-mark"></span><span class="f-brand-name"><b>Verdell</b><span>Tree Care</span></span></div>
<div class="abs f-social" style="left:65px;top:2675px" role="img" aria-label="Social profile"></div>
<div class="abs f-social" style="left:125px;top:2675px" role="img" aria-label="Social profile"></div>
<div class="abs f-social" style="left:186px;top:2675px" role="img" aria-label="Social profile"></div>
<div class="abs f-social" style="left:246px;top:2675px" role="img" aria-label="Social profile"></div>

<p class="abs f-head" style="left:374px;top:2578px">Contact Me</p>
<svg class="abs" style="left:382px;top:2615px" width="22" height="22" viewBox="0 0 24 24" fill="#fff"><path d="M6.6 10.8a15 15 0 006.6 6.6l2.2-2.2a1 1 0 011-.25 11.4 11.4 0 003.6.6 1 1 0 011 1V20a1 1 0 01-1 1A17 17 0 013 4a1 1 0 011-1h3.5a1 1 0 011 1c0 1.25.2 2.45.6 3.6a1 1 0 01-.25 1z"/></svg>
<p class="abs" style="left:419px;top:2617px;font-size:13px;font-weight:500;color:#fff">(555) 014-3827</p>
<svg class="abs" style="left:382px;top:2656px" width="24" height="20" viewBox="0 0 24 20" fill="none" stroke="#fff" stroke-width="1.8"><rect x="1" y="2" width="22" height="16" rx="2"/><path d="M1 3l11 8 11-8"/></svg>
<p class="abs" style="left:421px;top:2655px;font-size:16px;font-weight:500;color:#fff">hello@verdelltree.com</p>

<p class="abs f-head" style="left:624px;top:2578px">Menu</p>
<p class="abs f-item" style="left:624px;top:2613px">Home</p>
<p class="abs f-item" style="left:624px;top:2644px">About</p>
<p class="abs f-item" style="left:624px;top:2676px">Tree Care Services</p>
<p class="abs f-item" style="left:624px;top:2707px">Expert Advice Consulting</p>

<p class="abs f-news">Subcribe To Our Newslatter</p>
<div class="abs" style="left:814px;top:2605px;width:205px;height:29px;background:#fff;border-radius:3px"></div>
<div class="abs" style="left:1030px;top:2605px;width:30px;height:29px;background:#000;border-radius:3px">
  <svg width="30" height="29" viewBox="0 0 30 29"><path d="M9 8l13 6.5L9 21l2-6.5z" stroke="#fff" stroke-width="1.6" fill="none"/></svg></div>

<div class="abs rule"></div>
<p class="abs copy">Copyright © 2024 | Verdell Tree Care | All rights reserved.</p>

</body>
</html>
```